Gobal construction supply company needs new business card design

I need a business card design for my global supply company using an existing logo. i will be looking to print these on rounded corner cards with the black background version of my logo on the back. on the front white background, my logo again and my simple details.

```html
<!DOCTYPE html>
<html lang="en">
<head>
<meta charset="utf-8">
<title>Meridian Supply Works – Business Cards</title>
<link href="https://fonts.googleapis.com/css2?family=Montserrat:wght@400;500;700;800&display=swap" rel="stylesheet">
<style>
  :root {
    --backdrop: #3a3b3d;
    --card: #ffffff;
    --ink: #111111;
    --red: #d90000;
  }
  * { box-sizing: border-box; margin: 0; padding: 0; }
  html, body { width: 1200px; height: 1000px; overflow: hidden; }
  body {
    background: var(--backdrop);
    font-family: "Montserrat", Arial, sans-serif;
    color: var(--ink);
    position: relative;
  }
  .card {
    position: absolute;
    width: 700px;
    height: 400px;
    left: 250px;
    background: var(--card);
    border-radius: 28px;
    overflow: hidden;
  }
  .card--back { top: 60px; }
  .card--front { top: 540px; }

  .wordmark {
    position: absolute;
    font-weight: 800;
    color: var(--ink);
    text-transform: uppercase;
    letter-spacing: 0.5px;
    white-space: nowrap;
    text-align: center;
  }
  .card--back .wordmark {
    left: 0; right: 0; top: 50%;
    transform: translateY(-50%);
    font-size: 38px;
  }
  .card--front .wordmark {
    left: 20px; width: 310px; top: 150px;
    font-size: 21px;
  }

  .divider {
    position: absolute;
    left: 350px; top: 60px;
    width: 2px; height: 220px;
    background: var(--red);
  }
  .details {
    position: absolute;
    left: 378px; top: 66px;
    width: 300px;
  }
  .details__name {
    color: var(--red);
    font-weight: 700;
    font-size: 22px;
    text-transform: uppercase;
    letter-spacing: 0.3px;
  }
  .details__title { font-size: 14px; font-weight: 500; margin-top: 2px; }
  .details__address { font-size: 14px; font-weight: 500; line-height: 1.35; margin-top: 18px; }
  .contacts { list-style: none; margin-top: 14px; }
  .contacts li {
    display: flex; align-items: center; gap: 8px;
    font-size: 15px; font-weight: 500; line-height: 1.5;
  }
  .contacts svg { width: 13px; height: 13px; flex: none; fill: var(--red); }

  .base-rule {
    position: absolute; left: 0; right: 0; bottom: 44px;
    height: 4px; background: var(--ink);
  }
  .base-band {
    position: absolute; left: 0; right: 0; bottom: 0;
    height: 38px; background: var(--red);
  }
</style>
</head>
<body>

  <section class="card card--back" aria-label="Card back">
    <p class="wordmark">Meridian Supply Works</p>
  </section>

  <section class="card card--front" aria-label="Card front">
    <p class="wordmark">Meridian Supply Works</p>

    <div class="divider"></div>

    <div class="details">
      <p class="details__name">Marcus Hale</p>
      <p class="details__title">Managing Director</p>
      <p class="details__address">215 Larkin Avenue,<br>Tulsa, OK 74103</p>
      <ul class="contacts">
        <li><svg viewBox="0 0 16 16"><path d="M3 1h3l1.5 4-2 1.5a9 9 0 0 0 4 4L11 8.5l4 1.5v3a2 2 0 0 1-2 2A12 12 0 0 1 1 3a2 2 0 0 1 2-2z"/></svg>+1 (555) 210 4837</li>
        <li><svg viewBox="0 0 16 16"><path d="M4 0h8a1 1 0 0 1 1 1v14a1 1 0 0 1-1 1H4a1 1 0 0 1-1-1V1a1 1 0 0 1 1-1zm1 2v10h6V2zm3 11a1 1 0 1 0 0 2 1 1 0 0 0 0-2z"/></svg>+1 (555) 210 4838</li>
        <li><svg viewBox="0 0 16 16"><path d="M1 3h14v10H1zm1.5 1.2L8 8.5l5.5-4.3z"/></svg>marcus@meridiansw.com</li>
        <li><svg viewBox="0 0 16 16"><path d="M8 0a8 8 0 1 0 0 16A8 8 0 0 0 8 0zm0 1.5c.9 1 1.6 2.6 1.8 5H6.2c.2-2.4.9-4 1.8-5zM1.6 7h3.1c.1-2 .6-3.7 1.3-4.9A6.5 6.5 0 0 0 1.6 7zm9.7 0h3.1A6.5 6.5 0 0 0 10 2.1c.7 1.2 1.2 2.9 1.3 4.9zM1.6 9a6.5 6.5 0 0 0 4.4 4.9C5.3 12.7 4.8 11 4.7 9zm4.6 0c.2 2.4.9 4 1.8 5 .9-1 1.6-2.6 1.8-5zm5.1 0c-.1 2-.6 3.7-1.3 4.9A6.5 6.5 0 0 0 14.4 9z"/></svg>www.meridiansw.com</li>
      </ul>
    </div>

    <div class="base-rule"></div>
    <div class="base-band"></div>
  </section>

</body>
</html>
```